Coastline Premier Retreats Business Card Design

Design a business card for Coastline Premier Retreats. Look at the website for colors and reference. Card should have logo, name, title, office number, mobile number, email, URL and a tagline like, "Luxury Hotel & Resort Email Marketing" (This might change).

https://www.coastlinepremierretreats.example

The rest I will leave up to your imagination.

Contact Information for Business Card

Logo, name, title, office number, mobile number, email, URL and a tagline like, "Luxury Hotel & Resort Email Marketing" (This might change).

```html
<!DOCTYPE html>
<html lang="en">
<head>
<meta charset="utf-8">
<title>Coastline Premier Retreats – Business Card</title>
<link rel="stylesheet" href="https://fonts.googleapis.com/css2?family=Michroma&family=Ubuntu:wght@400;500;700&display=swap">
<style>
  :root {
    --bg: #2a2a2a;
    --card-light: #ffffff;
    --card-dark: #000000;
    --accent: #f57200;
    --ink: #111111;
    --ink-soft: #1c1c1c;
    --rule: #b5b5b5;
    --white: #ffffff;
  }
  * { box-sizing: border-box; margin: 0; padding: 0; }
  html, body {
    width: 1093px; height: 1200px; overflow: hidden;
    background: var(--bg);
    font-family: "Ubuntu", sans-serif;
  }
  .card {
    position: absolute;
    left: 265px;
    width: 580px; height: 356px;
    border-radius: 24px;
    overflow: hidden;
  }
  .card::after {
    content: ""; position: absolute; left: 0; right: 0; bottom: 0;
    height: 11px; background: var(--accent);
  }
  .card--front { top: 226px; background: var(--card-light); }
  .card--back { top: 621px; background: var(--card-dark); }

  .brand {
    position: absolute;
    font-family: "Ubuntu", sans-serif;
    font-weight: 700;
    text-transform: uppercase;
    text-align: center;
  }
  .brand__line { display: block; white-space: nowrap; }
  .card--front .brand {
    left: 30px; top: 158px; width: 222px;
    font-size: 18px; line-height: 21px; letter-spacing: 0.5px;
    color: var(--ink);
  }
  .card--back .brand {
    left: 0; right: 0; top: 140px;
    font-size: 31px; line-height: 36px; letter-spacing: 1px;
    color: var(--white);
  }

  .divider {
    position: absolute; left: 272px; top: 74px;
    width: 1px; height: 209px; background: var(--rule);
  }
  .person { position: absolute; left: 290px; top: 100px; }
  .person__name {
    font-family: "Michroma", sans-serif;
    font-size: 16px; font-weight: 400; color: var(--ink);
    letter-spacing: 0.5px; line-height: 1.1;
    -webkit-text-stroke: 0.6px var(--ink);
  }
  .person__title {
    font-size: 15px; color: var(--accent); margin-top: 2px;
  }
  .contacts {
    position: absolute; left: 290px; top: 153px;
    list-style: none;
  }
  .contacts__item {
    display: flex; align-items: center; gap: 7px;
    height: 21px; font-size: 15px; color: var(--ink-soft);
    white-space: nowrap;
  }
  .contacts__icon { width: 15px; height: 15px; flex: none; }
  .contacts__item--web { font-size: 14px; }
  .accent { color: var(--accent); }

  .tagline {
    position: absolute; left: 0; right: 0; top: 296px;
    text-align: center; font-size: 16px; color: var(--accent);
  }
</style>
</head>
<body>
  <section class="card card--front" aria-label="Business card front">
    <div class="brand"><span class="brand__line">Coastline Premier</span><span class="brand__line">Retreats</span></div>
    <div class="divider"></div>
    <div class="person">
      <h1 class="person__name">DANIEL MARSH</h1>
      <p class="person__title">Managing Director</p>
    </div>
    <ul class="contacts">
      <li class="contacts__item">
        <svg class="contacts__icon" viewBox="0 0 16 16" aria-hidden="true"><path fill="none" stroke="#f57200" stroke-width="1.8" stroke-linecap="round" d="M4 2 L6 5 L4.8 6.6 Q6.5 10 9.4 11.2 L11 10 L14 12 L12.6 14 Q6 14 2 4.8 Z M9.5 2.5 A4 4 0 0 1 13.5 6.5 M9.5 5 A1.6 1.6 0 0 1 11 6.5"/></svg>
        055-987 654 321
      </li>
      <li class="contacts__item">
        <svg class="contacts__icon" viewBox="0 0 16 16" aria-hidden="true"><rect x="4" y="1" width="8" height="14" rx="1.5" fill="none" stroke="#f57200" stroke-width="1.6"/><circle cx="8" cy="12.5" r="0.9" fill="#f57200"/></svg>
        055-987 654 321
      </li>
      <li class="contacts__item">
        <svg class="contacts__icon" viewBox="0 0 16 16" aria-hidden="true"><rect x="0.5" y="3" width="15" height="10" fill="#f57200"/><path d="M0.5 3 L8 9 L15.5 3 M0.5 13 L6 8 M15.5 13 L10 8" fill="none" stroke="#fff" stroke-width="1"/></svg>
        info@cpretreats.example
      </li>
      <li class="contacts__item contacts__item--web">
        <svg class="contacts__icon" viewBox="0 0 16 16" aria-hidden="true"><g fill="none" stroke="#f57200" stroke-width="1.3"><circle cx="8" cy="8" r="6.8"/><ellipse cx="8" cy="8" rx="3" ry="6.8"/><path d="M1.2 8 H14.8 M2.2 4.5 H13.8 M2.2 11.5 H13.8"/></g></svg>
        <span>www.<span class="accent">coastlinepremierretreats</span>.example</span>
      </li>
    </ul>
  </section>

  <section class="card card--back" aria-label="Business card back">
    <div class="brand"><span class="brand__line">Coastline Premier</span><span class="brand__line">Retreats</span></div>
    <p class="tagline">Luxury Hotel &amp; Resort Email Marketing</p>
  </section>
</body>
</html>
```